Judicial election website to attract voters

I need a simple one-page web design for a judicial election. I'm going to put up one picture, maybe two. The picture I have needs a little touch-up (whiten teeth for example). I have 3 paragraphs of text. I'd like a "Donate" button that can link to a CoinDrift account. I'd also like a little background design, like the Constitution or something like that. There's a couple other little things but that's the bulk of it.

Target Market(s)

Involved voters and some media

Industry/Entity Type

Legal

Number of Pages Required

1 page

Font styles to use
Sans Serif

Requirements
Must have
• My picture, text, donate button
• Phrase "Remember to vote August 30, 2016!"
Nice to have
• Perhaps a second photo, maybe a short 30 second video of me talking directly to the voters, cool background: Constitution, something judgey.
Should not have
• Not sure ... profanity, I guess.

```html
<!DOCTYPE html>
<html lang="en">
<head>
<meta charset="utf-8">
<title>Local Elections</title>
<link rel="stylesheet" href="https://fonts.googleapis.com/css2?family=Cinzel:wght@700&family=Lato:wght@400;700&family=Montserrat:wght@700&display=swap">
<style>
  :root {
    --navy: #0a1a6e;
    --red: #e0101a;
    --text: #333333;
    --rule: #e3e3e3;
    --white: #ffffff;
    --player: #1b1b1b;
  }
  * { box-sizing: border-box; margin: 0; padding: 0; }
  html, body { width: 1200px; height: 877px; overflow: hidden; background: var(--white); }
  body { font-family: "Lato", sans-serif; color: var(--text); position: relative; }

  .site-header {
    height: 112px;
    border-top: 3px solid var(--navy);
    position: relative;
  }
  .brand {
    position: absolute; left: 94px; top: 34px;
    font-family: "Lato", sans-serif; font-weight: 700;
    font-size: 36px; letter-spacing: 1px; color: var(--navy);
    text-transform: uppercase;
  }
  .donate-btn {
    position: absolute; left: 944px; top: 35px;
    width: 165px; height: 40px; border-radius: 3px;
    background: var(--navy); color: var(--white);
    display: flex; align-items: center; justify-content: center; gap: 9px;
    font-family: "Lato", sans-serif; font-weight: 700; font-size: 16px;
    letter-spacing: 0.4px; text-decoration: none;
  }

  .hero {
    position: absolute; left: 0; top: 112px; width: 1200px; height: 348px;
    background: linear-gradient(90deg, #7d8490 0%, #a4a7ab 30%, #c9c2b4 55%, #bfb6a6 75%, #c58a73 92%, #b7ab9a 100%);
  }
  .hero-title {
    position: absolute; left: 100px; top: 190px; width: 556px;
    text-align: center; color: var(--white);
    font-family: "Montserrat", sans-serif; font-weight: 700;
    font-size: 45px; line-height: 57px; text-transform: uppercase;
    text-shadow: 0 2px 6px rgba(0,0,0,0.45);
  }

  .about {
    position: absolute; left: 90px; top: 505px; width: 630px;
  }
  .about-title {
    font-family: "Cinzel", serif; font-weight: 700;
    font-size: 31px; color: var(--navy); letter-spacing: 1px;
    padding: 0 0 7px 2px; border-bottom: 1px solid var(--rule);
  }
  .about-title .accent { color: var(--red); }
  .about-body { padding: 20px 0 0 3px; }
  .about-body p { font-size: 14px; line-height: 21.4px; margin-bottom: 8px; }

  .video {
    position: absolute; left: 736px; top: 509px; width: 373px; height: 272px;
    background: var(--player); overflow: hidden;
  }
  .video-still {
    position: absolute; inset: 0 0 28px 0;
    background: radial-gradient(ellipse at 50% 45%, #4a5478 0%, #262a3a 50%, #0d0d12 100%);
  }
  .video-play {
    position: absolute; left: 152px; top: 96px; width: 68px; height: 50px;
    border-radius: 12px; background: rgba(20,20,20,0.75);
    display: flex; align-items: center; justify-content: center;
  }
  .video-controls {
    position: absolute; left: 0; bottom: 0; width: 100%; height: 28px;
    background: #151515; display: flex; align-items: center;
    color: var(--white); font-size: 12px; font-weight: 700;
  }
  .ctrl-play { width: 38px; height: 28px; background: #2b2b2b; display: flex; align-items: center; justify-content: center; }
  .time { padding: 0 8px; }
  .track { flex: 1; height: 8px; border-radius: 4px; background: #3d3d3d; position: relative; }
  .track::after { content: ""; position: absolute; left: 101px; top: -1px; width: 10px; height: 10px; border-radius: 50%; background: #666; }
  .ctrl-icon { width: 34px; display: flex; justify-content: center; }

  .site-footer {
    position: absolute; left: 0; top: 834px; width: 1200px; height: 43px;
    background: var(--navy); color: var(--white);
    display: flex; align-items: center; justify-content: center;
    font-size: 13.5px;
  }
</style>
</head>
<body>
  <header class="site-header">
    <div class="brand">Local Elections</div>
    <a class="donate-btn" href="#">
      <svg width="22" height="22" viewBox="0 0 22 22" aria-hidden="true">
        <circle cx="11" cy="11" r="9" fill="none" stroke="#fff" stroke-width="2"/>
        <path d="M11 5v12M8 8h4.5a2 2 0 0 1 0 4h-3a2 2 0 0 0 0 4H14" fill="none" stroke="#fff" stroke-width="1.8"/>
      </svg>
      DONATE NOW
    </a>
  </header>

  <section class="hero" role="img" aria-label="American flag waving before a capitol dome, with a portrait of the smiling candidate on the right">
    <h1 class="hero-title">Remember to vote<br>August 30, 2016!</h1>
  </section>

  <section class="about">
    <h2 class="about-title">ABOUT <span class="accent">ME</span></h2>
    <div class="about-body">
      <p>Lorem ipsum dolor sit amet, consectetuer adipiscing elit, sed diam nonummy nibh euismod tincidunt ut laoreet dolore magna aliquam erat volutpat. Ut wisi enim ad minim veniam, quis nostrud exerci tation ullamcorper suscipit lobortis nisl ut aliquip ex ea commodo consequat.</p>
      <p>Duis autem vel eum iriure dolor in hendrerit in vulputate velit esse molestie consequat, vel illum Ut wisi enim ad minim veniam, quis nostrud exerci tation ullamcorper suscipit lobortis nisl ut aliquip ex ea commododolore eu feugiat nulla facilisis at vero eros et accumsan et.</p>
      <p>Lusto odio dignissim qui blandit praesent luptatum zzril delenit augue duis dolore te feugait nulla dolor in hendrerit in vulputate velit esse molestie consequat, vel illum dolore eu feugiat.</p>
    </div>
  </section>

  <div class="video">
    <div class="video-still" role="img" aria-label="Video still of a speaker with microphone addressing a crowd at a campaign rally"></div>
    <div class="video-play">
      <svg width="20" height="22" viewBox="0 0 20 22" aria-hidden="true"><path d="M2 1l17 10L2 21z" fill="#fff"/></svg>
    </div>
    <div class="video-controls">
      <div class="ctrl-play"><svg width="12" height="14" viewBox="0 0 12 14" aria-hidden="true"><path d="M0 0l12 7L0 14z" fill="#fff"/></svg></div>
      <span class="time">04:59</span>
      <div class="track"></div>
      <span class="time">10:35</span>
      <div class="ctrl-icon"><svg width="18" height="16" viewBox="0 0 18 16" aria-hidden="true"><path d="M0 5h4l5-4v14l-5-4H0z" fill="#fff"/><path d="M12 4a5 5 0 0 1 0 8M14 2a8 8 0 0 1 0 12" fill="none" stroke="#fff" stroke-width="1.5"/></svg></div>
      <div class="ctrl-icon"><svg width="18" height="18" viewBox="0 0 18 18" aria-hidden="true"><path d="M1 1h6L5 3l4 4-2 2-4-4-2 2zM17 17h-6l2-2-4-4 2-2 4 4 2-2z" fill="#fff"/></svg></div>
    </div>
  </div>

  <footer class="site-footer">Copyright © 2016 Local Elections. All Rights Reserved.</footer>
</body>
</html>
```